New Modern Wix Website Design

We are NOT your typical electrical/home improvement contractor, so we need our website updated. We already have a logo for each division.
We provided a neutral logo with a hard hat, a logo for the home improvement, and a logo for the electrical division. (if we can implement all 3 logos will be great but at least the 2 for the divisions must be used.

We looking for a website that a 10-year-old can understand, our target audience is the new young generation that wants innovations in their properties, smart homes, cool smart things/gadgets. So we need a website that is fun, simple, eye-catching. (we don't want to appear TOO serious and boring)
NO GENERIC WEBSITES SO MUST BE VERY CREATIVE!!!

We want to be able to share google reviews, a contact box, business hours, our services, etc...

current website kelvantrio.example

Target Market(s)

Contractors in different trades.

Industry/Entity Type

Construction

Colors
FFC000
F8CF3A
FAE287
FDF2CF
FEFAEE

Requirements
Must have
• Modern upmarket look and feel
Nice to have
• already attached supporting images.
Should not have
• basic typical construction boring and depressing look and feel.

```html
<!DOCTYPE html>
<html lang="en">
<head>
<meta charset="utf-8">
<title>Kelvantrio — Electrical &amp; Home Improvement</title>
<link href="https://fonts.googleapis.com/css2?family=Roboto:wght@300;400;500;700&family=Oswald:wght@500&display=swap" rel="stylesheet">
<style>
:root{
  --gold:#b8862b;
  --gold-bright:#d99c2b;
  --ink:#222;
  --text:#555;
  --grey-band:#5e5e60;
  --footer:#3a3a3c;
  --white:#fff;
}
*{margin:0;padding:0;box-sizing:border-box}
html,body{width:1200px;height:4161px;overflow:hidden}
body{position:relative;font-family:'Roboto',sans-serif;color:var(--text);background:var(--white)}
.abs{position:absolute}
.photo{position:absolute}

/* hero */
.hero{position:absolute;left:0;top:0;width:1200px;height:660px;overflow:hidden}
.hero-photo{position:absolute;inset:0;background:linear-gradient(180deg,#d3e1ec 0%,#9fb4c6 22%,#6d6a5e 48%,#4d5c3b 72%,#6f6c40 100%)}
.hero-curve{position:absolute;left:0;top:520px}
.topbar{position:absolute;top:14px;right:110px;display:flex;gap:30px;font-size:11px;color:#333}
.topbar span b{font-weight:700;font-size:13px;margin-left:6px}
.topbar svg{vertical-align:-2px;margin-right:5px}
.brand{position:absolute;left:113px;top:66px;display:flex;align-items:center;gap:10px;font-weight:700;font-size:22px;color:#111}
.brand i{display:block;width:14px;height:14px;border-radius:50%;background:var(--gold)}
.nav{position:absolute;top:66px;right:110px;display:flex;gap:34px;font-size:12px;color:#333;align-items:center}
.nav .active{color:var(--gold);border-bottom:1px solid var(--gold);padding-bottom:6px;margin-top:6px}
.nav .sq{width:11px;height:11px;background:#222;display:inline-block;margin-left:-14px}
.hero-title{position:absolute;top:265px;width:1200px;text-align:center;font-family:'Oswald',sans-serif;font-weight:500;font-size:66px;color:#fff;letter-spacing:1px}
.down{position:absolute;left:579px;top:612px;width:42px;height:42px;border-radius:50%;background:var(--gold);display:flex;align-items:center;justify-content:center}

/* headings */
.h2{font-size:32px;font-weight:400;color:var(--ink);text-transform:uppercase;line-height:1.15}
.h2 b{color:var(--gold);font-weight:700}
.rule{display:flex;align-items:center;gap:12px}
.rule span{display:block;height:2px;width:38px;background:var(--gold)}
.rule span.dark{background:#222}
.rule i{display:block;width:10px;height:10px;background:var(--gold);transform:rotate(45deg)}
.btn{position:absolute;display:flex;align-items:center;justify-content:center;border-radius:24px;font-size:14px;font-weight:700;text-transform:uppercase}

/* about */
.about-tab{left:286px;top:732px;width:137px;height:24px;background:#111;clip-path:polygon(0 0,100% 0,92% 100%,8% 100%)}
.about-circle{left:170px;top:751px;width:380px;height:380px;border-radius:50%;border:4px solid var(--gold);background:linear-gradient(180deg,#5b8fcf 0%,#a9c7e8 40%,#ecebe6 58%,#8a7a64 70%,#6c8f45 100%)}
.about-house{left:90px;top:870px;width:200px;height:175px;background:linear-gradient(180deg,#f2f2ef 0%,#d7d4cd 55%,#7a8a5a 100%)}
.about-text{left:610px;top:718px;width:430px}
.about-text p{font-size:14px;line-height:24px;margin-top:14px}
.sub{font-size:19px;color:var(--ink);margin-top:14px}

/* services */
.services{left:0;top:1210px;width:1200px;height:612px;background:var(--grey-band)}
.services .h2{color:#fff;text-align:center}
.card{position:absolute;top:168px;width:439px;height:358px;border:3px solid #444}
.card .frame{position:absolute;inset:8px;border:3px solid var(--gold-bright)}
.card .label{position:absolute;bottom:14px;width:100%;text-align:center;color:#fff;font-size:21px;letter-spacing:1px;font-weight:500}

/* testimonials */
.t-photo{left:218px;top:1985px;width:465px;height:226px;border:2px solid var(--gold);background:linear-gradient(180deg,#263b2f 0%,#6e7d73 40%,#e8e4dc 62%,#586a4a 100%)}
.t-box{left:703px;top:1985px;width:276px;height:226px;border:1px solid #ddd;padding:14px 10px;font-size:11.5px;line-height:19.5px;color:#666}
.arrow{position:absolute;width:48px;height:48px;border:2px solid var(--gold);display:flex;align-items:center;justify-content:center}
.dots{left:615px;top:2234px;display:flex;gap:2px}
.dots i{width:7px;height:7px;border:1px solid #999;display:block}
.dots i.on{background:var(--gold);border-color:var(--gold)}

/* business */
.business{left:0;top:2330px;width:1200px;height:624px;background:var(--gold-bright);overflow:hidden}
.business .h2{color:#fff}
.business .h2 b{color:#fff}
.business p{color:#fff;font-size:14px;line-height:24px}
.biz-tab{left:776px;top:110px;width:138px;height:24px;background:#111;clip-path:polygon(0 0,100% 0,92% 100%,8% 100%)}
.biz-circle{left:658px;top:127px;width:380px;height:380px;border-radius:50%;border:4px solid #fff;background:linear-gradient(180deg,#3a6fc3 0%,#9cc0ea 38%,#d9d2c4 52%,#5a5f6b 62%,#9a917f 100%)}
.biz-house{left:600px;top:240px;width:600px;height:215px;clip-path:polygon(12% 30%,40% 0,70% 10%,100% 35%,100% 100%,0 100%,0 45%);background:linear-gradient(180deg,#4f5460 0%,#6b7079 45%,#c9a56d 75%,#8b8475 100%)}

/* contact */
.contact-frame{left:192px;top:3054px;width:816px;height:455px;border:4px solid var(--gold)}
.contact-head{left:450px;top:3030px;width:300px;background:#fff;text-align:center}
.ic{position:absolute;width:60px;height:60px;border-radius:50%;border:2px solid var(--gold);display:flex;align-items:center;justify-content:center}
.ic-label{position:absolute;font-size:13px;color:#666}
.ic-label b{display:block;color:var(--gold);font-size:16px;margin-top:4px}
.field{position:absolute;border:1px solid #aaa;display:flex;align-items:center;gap:10px;padding-left:12px;font-size:11px;color:#777}
.field.msg{align-items:flex-start;padding-top:14px}

/* footer */
.footer{left:0;top:3600px;width:1200px;height:561px}
.sub-title{left:208px;top:3730px;color:#fff;font-size:27px}
.sub-input{left:475px;top:3721px;width:468px;height:50px;border-radius:25px;background:#fff;border:2px solid var(--gold)}
.footer-rule{left:111px;width:978px;height:1px;background:#777}
.f-brand{left:116px;top:3985px;display:flex;align-items:center;gap:10px;color:var(--gold);font-weight:700;font-size:30px}
.f-brand i{display:block;width:16px;height:16px;border-radius:50%;background:var(--gold)}
.f-col{position:absolute;top:3862px}
.f-col h4{color:#fff;font-size:19px;font-weight:700}
.f-col h4::after{content:"";display:block;width:40px;height:2px;background:var(--gold);margin-top:10px}
.f-col a{display:block;color:#ccc;font-size:12px;line-height:24px;text-decoration:none}
.f-col ul{list-style:none;margin-top:22px}
.legal{top:4116px;font-size:13px;color:#ccc}
</style>
</head>
<body>

<header class="hero">
  <div class="hero-photo" role="img" aria-label="Modern brick house with solar roof panels and an open glass wall at dusk"></div>
  <div class="topbar">
    <span><svg width="10" height="13" viewBox="0 0 10 13"><path d="M5 0a5 5 0 0 0-5 5c0 4 5 8 5 8s5-4 5-8a5 5 0 0 0-5-5z" fill="#b8862b"/><circle cx="5" cy="5" r="2" fill="#fff"/></svg>Address<b>Ashford, PA 17000</b></span>
    <span><svg width="14" height="10" viewBox="0 0 14 10"><rect width="14" height="10" fill="#b8862b"/><path d="M0 0l7 6 7-6" stroke="#fff" fill="none"/></svg>Email Us<b>info@kelvantrio.example</b></span>
    <span><svg width="12" height="12" viewBox="0 0 22 22"><path d="M5 2l4 4-2 3q2 4 6 6l3-2 4 4-3 3Q9 19 2 5z" fill="#b8862b"/></svg>Contact Us Today<b>+1 (555) 014-2290</b></span>
  </div>
  <div class="brand"><i></i>KELVANTRIO</div>
  <nav class="nav">
    <span class="active">HOME</span><span>ABOUT</span><span>JOB OPPORTUNITIES</span><span>CONTACT</span><span>ABOUT</span><span>MORE</span><span style="color:#aaa">|</span><span class="sq"></span>
  </nav>
  <h1 class="hero-title">KELVANTRIO</h1>
  <svg class="hero-curve" width="1200" height="140" viewBox="0 0 1200 140">
    <path d="M0 30 Q600 160 1200 30 L1200 140 L0 140Z" fill="#fff"/>
    <path d="M0 30 Q600 160 1200 30 L1200 42 Q600 150 0 42Z" fill="#b8862b"/>
    <path d="M468 104 Q600 112 735 104 L735 110 Q600 118 468 110Z" fill="#111"/>
  </svg>
  <div class="down"><svg width="14" height="9" viewBox="0 0 14 9"><path d="M1 1l6 6 6-6" stroke="#fff" stroke-width="2" fill="none"/></svg></div>
</header>

<section>
  <div class="abs about-tab"></div>
  <div class="photo about-circle" role="img" aria-label="Modern white and timber two-storey house with garage"></div>
  <div class="photo about-house" role="img" aria-label="Front extension of the modern house with lawn and flowers"></div>
  <div class="abs about-text">
    <h2 class="h2">About <b>Us</b></h2>
    <div class="rule" style="margin-top:10px"><span></span><i></i><span class="dark"></span></div>
    <div class="sub">The Full Story</div>
    <p>As licensed contractors, we provide our clients with a comprehensive approach to all of their projects, specializing in a wide range of services. Since we founded our business in 2016, we've been committed to our client's needs and satisfaction.</p>
    <p style="margin-top:20px">Do you have a project or idea in mind that you want to get started on? We are here to make it happen. Get in touch to learn what we can do for you today.</p>
  </div>
  <div class="btn" style="left:610px;top:1072px;width:173px;height:44px;background:var(--gold);border:2px solid #222;color:#fff">Learn More</div>
</section>

<section class="abs services">
  <h2 class="h2" style="margin-top:80px">Our <b>Services</b></h2>
  <div class="rule" style="justify-content:center;margin-top:8px"><span style="background:#fff;width:56px"></span><i></i><span style="background:#fff;width:56px"></span></div>
  <div class="card" style="left:128px;background:linear-gradient(90deg,#3b5f9a 0%,#6d87b0 40%,#8d8f8e 70%,#5c5f5e 100%)" role="img" aria-label="Electrician reviewing plans beside an open electrical panel">
    <div class="frame"></div><div class="label">ELECTRICAL SERVICES</div>
  </div>
  <div class="card" style="left:633px;background:linear-gradient(180deg,#9aa6b4 0%,#4c4e52 45%,#a97e4f 70%,#3c3a36 100%)" role="img" aria-label="Modern home with timber cladding and solar roof at dusk">
    <div class="frame"></div><div class="label">HOME IMPROVEMENT</div>
  </div>
</section>

<section>
  <h2 class="abs h2" style="top:1888px;width:1200px;text-align:center">Our <b>Testimonials</b></h2>
  <div class="abs rule" style="top:1937px;width:1200px;justify-content:center"><span style="width:130px"></span><i></i><span style="width:130px"></span></div>
  <div class="arrow" style="left:128px;top:2075px"><svg width="8" height="12" viewBox="0 0 8 12"><path d="M7 1L2 6l5 5" stroke="#222" stroke-width="2" fill="none"/></svg></div>
  <div class="photo t-photo" role="img" aria-label="Contemporary multi-level house with wood accents and landscaped garden"></div>
  <div class="abs t-box">
    Dolorsit amet consectetur adipiscing elit seddo eiusmod tempor incididuntut labore etdolore magna aliqua. Utenim adminim veniam quis nostrud exercitati onenimad minim veniam quis nostrud exercitation ullamco laboris nisi utaliqu ipexea commodo consequat
    <div style="margin-top:12px;display:flex;align-items:center;gap:10px;color:#222;font-size:13px;font-weight:500"><span style="width:24px;height:1px;background:var(--gold)"></span>DANIEL REEVE</div>
    <div style="margin-top:12px;text-align:center;font-size:12px"><span style="display:inline-block;width:12px;height:12px;border-radius:50%;background:#c9c9c9;vertical-align:-2px;margin-right:5px"></span>2 Days ago</div>
  </div>
  <div class="arrow" style="left:1001px;top:2075px"><svg width="8" height="12" viewBox="0 0 8 12"><path d="M1 1l5 5-5 5" stroke="#222" stroke-width="2" fill="none"/></svg></div>
  <div class="abs dots"><i></i><i></i><i></i><i class="on"></i><i></i><i></i></div>
</section>

<section class="abs business">
  <div class="abs" style="left:142px;top:96px;width:440px">
    <h2 class="h2">Our <b>Business</b></h2>
    <div class="rule" style="margin-top:10px"><span style="background:#fff;width:82px"></span><i style="background:#fff"></i><span class="dark" style="width:82px"></span></div>
    <div style="color:#fff;font-size:19px;font-weight:500;margin-top:14px">Quality &amp; Integrity</div>
    <p style="margin-top:14px">Kelvantrio is completely dedicated to client satisfaction. All of our team members are punctual and knowledgeable, helping make us some of the most trusted contractors in the industry. We've come a long way since our founding in 2016, but the leading operating values behind our services, to work with integrity in order to provide high-quality services to our clients, remain unchanged.</p>
    <p style="margin-top:19px;width:380px">Please get in touch with any inquiries. Be sure to include your contact information as well as any important details about your needs.</p>
  </div>
  <div class="btn" style="left:142px;top:495px;width:170px;height:43px;background:#fff;border:2px solid #222;color:var(--gold)">Learn More</div>
  <div class="abs biz-tab"></div>
  <div class="photo biz-circle" role="img" aria-label="Large grey family house with gables at twilight"></div>
  <div class="photo biz-house" role="img" aria-label="Lit front of the family house with double garage and driveway"></div>
</section>

<section>
  <div class="abs contact-frame"></div>
  <div class="abs contact-head">
    <h2 class="h2">Contact <b>Us</b></h2>
    <div class="rule" style="justify-content:center;margin-top:6px"><span style="width:62px"></span><i></i><span class="dark" style="width:62px"></span></div>
  </div>
  <div class="ic" style="left:370px;top:3110px"><svg width="22" height="22" viewBox="0 0 22 22"><path d="M5 2l4 4-2 3q2 4 6 6l3-2 4 4-3 3Q9 19 2 5z" fill="#333"/></svg></div>
  <div class="ic-label" style="left:443px;top:3122px">CALL US<b>+1 (555) 014-2290</b></div>
  <div class="ic" style="left:648px;top:3110px"><svg width="24" height="16" viewBox="0 0 24 16"><rect width="24" height="16" fill="#333"/><path d="M0 0l12 9 12-9" stroke="#fff" stroke-width="1.5" fill="none"/></svg></div>
  <div class="ic-label" style="left:721px;top:3122px">E MAIL<b>info@kelvantrio.example</b></div>

  <div class="field" style="left:276px;top:3188px;width:312px;height:44px"><svg width="11" height="12"><circle cx="5.5" cy="3.5" r="3" fill="#333"/><path d="M0 12q5.5-8 11 0z" fill="#333"/></svg>FIRST NAME</div>
  <div class="field" style="left:614px;top:3188px;width:311px;height:44px"><svg width="11" height="12"><circle cx="5.5" cy="3.5" r="3" fill="#333"/><path d="M0 12q5.5-8 11 0z" fill="#333"/></svg>LAST NAME</div>
  <div class="field" style="left:276px;top:3249px;width:312px;height:44px"><svg width="14" height="10"><rect width="14" height="10" fill="#333"/><path d="M0 0l7 6 7-6" stroke="#fff" fill="none"/></svg>EMAIL</div>
  <div class="field" style="left:614px;top:3249px;width:311px;height:44px"><svg width="12" height="12" viewBox="0 0 22 22"><path d="M5 2l4 4-2 3q2 4 6 6l3-2 4 4-3 3Q9 19 2 5z" fill="#333"/></svg>PHONE</div>
  <div class="field msg" style="left:276px;top:3311px;width:649px;height:129px"><svg width="12" height="12"><path d="M1 1l10 10" stroke="#333" stroke-width="2"/></svg>MESSAGE</div>
  <div class="btn" style="left:513px;top:3487px;width:172px;height:43px;background:var(--gold);border:2px solid #222;color:#fff">Submit</div>
</section>

<footer class="abs footer">
  <svg class="abs" style="left:0;top:0" width="1200" height="561" viewBox="0 0 1200 561">
    <path d="M0 98 Q600 -40 1200 98 L1200 561 L0 561Z" fill="#3a3a3c"/>
    <path d="M0 92 Q600 -46 1200 92 L1200 104 Q600 -32 0 104Z" fill="#b8862b"/>
    <path d="M468 28 Q600 12 735 28 L735 36 Q600 20 468 36Z" fill="#111"/>
  </svg>
</footer>
<div class="abs sub-title">SUBSCRIBE FORM</div>
<div class="abs sub-input">
  <div class="abs" style="left:18px;top:15px;font-size:12px;color:#666;display:flex;gap:10px;align-items:center"><svg width="14" height="10"><rect width="14" height="10" fill="#333"/><path d="M0 0l7 6 7-6" stroke="#fff" fill="none"/></svg>ENTER EMAIL</div>
  <div class="btn" style="left:290px;top:2px;width:172px;height:42px;background:var(--gold);border:2px solid #222;color:#fff">Submit</div>
</div>
<div class="abs footer-rule" style="top:3824px"></div>
<div class="abs f-brand"><i></i>KELVANTRIO</div>
<div class="f-col" style="left:396px"><h4>QUICK LINKS</h4><ul><li><a>HOME</a></li><li><a>ABOUT</a></li><li><a>JOB OPPORTUNITIES</a></li><li><a>CONTACT</a></li><li><a>ABOUT</a></li><li><a>MORE</a></li></ul></div>
<div class="f-col" style="left:589px"><h4>OUR POLICIES</h4><ul><li><a>TERMS &amp; CONDITIONS</a></li><li><a>PRIVACY POLICY</a></li><li><a>COMPANY VALUES</a></li><li><a>CORPORATE ETHICS POLICY</a></li><li><a>ANTI SLAVERY POLICY</a></li></ul></div>
<div class="f-col" style="left:833px"><h4>SUPPORT</h4><ul><li><a>TEAM</a></li><li><a>ABOUT US</a></li><li><a>CAREERS</a></li><li><a>OUR VALUES</a></li></ul></div>
<div class="f-col" style="left:995px"><h4>LINKS</h4><ul><li><a>COPYRIGHT</a></li><li><a>LEGAL</a></li><li><a>PRIVACY</a></li><li><a>ACCESSIBILITY</a></li><li><a>SITEMAP</a></li></ul></div>
<div class="abs footer-rule" style="top:4089px"></div>
<div class="abs legal" style="left:113px">Privacy Policy</div>
<div class="abs" style="left:222px;top:4106px;width:1px;height:30px;background:#999"></div>
<div class="abs legal" style="left:245px">Terms of Use</div>
<div class="abs legal" style="left:915px">©2021.All rights reserved.</div>
<div class="abs" style="left:1120px;top:4064px;width:44px;height:44px;border-radius:50%;background:var(--gold);display:flex;align-items:center;justify-content:center"><svg width="12" height="8" viewBox="0 0 12 8"><path d="M1 7l5-5 5 5" stroke="#fff" stroke-width="2" fill="none"/></svg></div>

</body>
</html>
```